Allied Health team of Physiotherapists & Occupational Therapists seek a business card design

We have our new logo, we now need our new business cards and stationary. Tidewell: Oedema & Family Clinic is seeking a generic card design to represent our whole team and individual cards for each therapist that incorporates our new logo to communicate our holistic approach that is calming, nuturing, supportive and welcoming.
Our Physiotherapists and Occupational Therapists assess, treat and provide education for people who are at risk of or who have lymphoedema. This is often as a result of treatment for cancer. We provide pre-operative and post-operative management and cancer rehabilitation in our Pilates studio. Our team also consists of Physiotherapists who have a strong interest in pelvic floor and continence management for both men and women.

Target Market(s)

Mainly women health conscious

Industry/Entity Type

Allied Health: Physiotherapy / Occupational Therapy

Contact Information for Business Card

Address: 14 Gallivant Ave Baywater 3277 Phone: 84316570 fax: 8431 6578 Email: info@tidewellcareservices.com.au Website: tidewellcareservices.com.au Facebook address: facebook.com/TidewellOedemaAndFamilyCareClinic. Room to write appointments. Individual cards need to have name, office email and individual email and professional details

Requirements
Must have
• Logo as per uploaded documents

```html
<!DOCTYPE html>
<html lang="en">
<head>
<meta charset="utf-8">
<title>Tidewell Business Card</title>
<link rel="stylesheet" href="https://fonts.googleapis.com/css2?family=Jost:wght@300;400;500&family=Lato:ital,wght@1,700&display=swap">
<style>
  :root {
    --stage: #131315;
    --cream: #fefbd8;
    --peach: #f9af7e;
    --sage: #bfc9bc;
    --ink: #2b2b2b;
    --white: #fffdf3;
  }
  * { margin: 0; padding: 0; box-sizing: border-box; }
  html, body { width: 1200px; height: 886px; overflow: hidden; background: var(--stage); }
  body { position: relative; font-family: "Jost", sans-serif; color: var(--ink); }
  .card {
    position: absolute; width: 447px; height: 256px; overflow: hidden;
    background: var(--cream);
    box-shadow: 0 18px 40px rgba(0,0,0,.55);
  }
  .card-front { left: 223px; top: 141px; }
  .card-back { left: 530px; top: 489px; }
  .card-shapes { position: absolute; inset: 0; }
  .holder-name {
    position: absolute; right: 16px; top: 30px;
    font-family: "Lato", sans-serif; font-style: italic; font-weight: 700;
    font-size: 25px; letter-spacing: .2px; color: var(--ink);
  }
  .holder-role {
    position: absolute; right: 16px; top: 63px;
    font-size: 12.5px; font-weight: 400; color: var(--ink);
  }
  .brand-mark {
    position: absolute; left: 299px; top: 124px; width: 116px; height: 116px;
    display: flex; flex-direction: column; align-items: center; justify-content: center; gap: 6px;
  }
  .brand-dot { width: 10px; height: 10px; border-radius: 50%; background: var(--white); }
  .brand-name { font-size: 22px; font-weight: 400; color: var(--white); letter-spacing: .5px; }
  .credentials { position: absolute; left: 21px; top: 96px; list-style: none; width: 210px; }
  .credentials li {
    position: relative; padding-left: 12px;
    font-size: 10.5px; font-weight: 300; line-height: 15px;
  }
  .credentials li::before {
    content: ""; position: absolute; left: 0; top: 5px;
    width: 5px; height: 5px; border-radius: 50%; background: var(--peach);
  }
  .services { position: absolute; left: 17px; top: 193px; }
  .services p { font-size: 10.8px; font-weight: 500; line-height: 15px; }
  .contact-list { position: absolute; left: 24px; top: 96px; list-style: none; }
  .contact-list li {
    display: flex; align-items: center; gap: 4px;
    height: 17.5px; font-size: 12px; font-weight: 400; color: var(--white);
  }
  .contact-list .phone { letter-spacing: 1.6px; font-size: 12.5px; }
  .contact-list svg { width: 13px; height: 13px; flex: none; }
  .appointment {
    position: absolute; left: 41px; top: 223px;
    font-size: 12px; color: var(--white);
  }
  .appointment span { letter-spacing: 1px; opacity: .9; }
</style>
</head>
<body>

<section class="card card-front" aria-label="Business card front">
  <svg class="card-shapes" viewBox="0 0 447 256" aria-hidden="true">
    <path d="M219 0 L240 0 L272 236 Q273 245 265 245 L259 245 Q251 245 249 237 Z" fill="var(--sage)"/>
    <path d="M236 0 L447 0 L447 256 L291 256 Q282 256 280 247 Z" fill="var(--peach)"/>
  </svg>
  <h1 class="holder-name">Maren Talbot</h1>
  <p class="holder-role">Physiotherapist</p>
  <div class="brand-mark">
    <span class="brand-dot"></span>
    <span class="brand-name">Tidewell</span>
  </div>
  <ul class="credentials">
    <li>B. Physio (Hons), B.App.Sci.<br>(Human Movement/Psych)</li>
    <li>Post Grad Certif. Exercise for Women</li>
    <li>Post Grad Certif. Continence &amp; Pelvic<br>Floor Rehabilitation</li>
  </ul>
  <div class="services">
    <p>Lymphoedema &amp; Oncology Rehabilitation</p>
    <p>Continence &amp; Pelvic Floor</p>
  </div>
</section>

<section class="card card-back" aria-label="Business card back">
  <svg class="card-shapes" viewBox="0 0 447 256" aria-hidden="true">
    <path d="M287 22 Q286 14 296 14 L299 14 Q306 14 308 22 L347 256 L330 256 Z" fill="var(--sage)"/>
    <path d="M0 0 L272 0 Q280 0 282 9 L328 256 L0 256 Z" fill="var(--peach)"/>
  </svg>
  <ul class="contact-list">
    <li class="phone">
      <svg viewBox="0 0 14 14" aria-hidden="true"><circle cx="7" cy="7" r="6" fill="none" stroke="var(--white)" stroke-width="1.1"/><path d="M4.6 3.8 L5.6 3.6 L6.2 5.2 L5.5 5.8 Q6.1 7.4 7.9 8.4 L8.5 7.7 L10 8.3 L9.9 9.3 Q7.9 10 5.9 8 Q3.9 6 4.6 3.8 Z" fill="var(--white)"/></svg>
      8431 6570
    </li>
    <li class="phone">
      <svg viewBox="0 0 14 14" aria-hidden="true"><circle cx="7" cy="7" r="6" fill="none" stroke="var(--white)" stroke-width="1.1"/><rect x="4" y="6" width="6" height="4" rx=".6" fill="var(--white)"/><rect x="5" y="3.8" width="4" height="2.4" fill="none" stroke="var(--white)" stroke-width=".8"/></svg>
      8431 6578
    </li>
    <li>
      <svg viewBox="0 0 14 14" aria-hidden="true"><circle cx="7" cy="7" r="6" fill="none" stroke="var(--white)" stroke-width="1.1"/><rect x="3.8" y="4.8" width="6.4" height="4.4" rx=".5" fill="var(--white)"/><path d="M3.8 5 L7 7.4 L10.2 5" fill="none" stroke="var(--peach)" stroke-width=".8"/></svg>
      info@tidewellcareservices.com.au
    </li>
    <li>
      <svg viewBox="0 0 14 14" aria-hidden="true"><circle cx="7" cy="7" r="6" fill="none" stroke="var(--white)" stroke-width="1.1"/></svg>
      TidewellOedemaAndFamilyCareClinic
    </li>
    <li>
      <svg viewBox="0 0 14 14" aria-hidden="true"><circle cx="7" cy="7" r="6" fill="none" stroke="var(--white)" stroke-width="1.1"/><circle cx="7" cy="7" r="3.4" fill="none" stroke="var(--white)" stroke-width=".8"/><path d="M3.6 7 H10.4 M7 3.6 V10.4" stroke="var(--white)" stroke-width=".7"/></svg>
      tidewellcareservices.com.au
    </li>
    <li>
      <svg viewBox="0 0 14 14" aria-hidden="true"><circle cx="7" cy="7" r="6" fill="none" stroke="var(--white)" stroke-width="1.1"/><path d="M7 11 Q4.3 7.8 4.3 6.1 A2.7 2.7 0 0 1 9.7 6.1 Q9.7 7.8 7 11 Z" fill="var(--white)"/><circle cx="7" cy="6.1" r="1" fill="var(--peach)"/></svg>
      14 Gallivant Ave, Baywater 3277
    </li>
  </ul>
  <p class="appointment">Next Appointment <span>.........................</span></p>
</section>

</body>
</html>
```